Upmarket Dessert Lounge needs a Business Card Design

We are an upmarket dessert lounge needing a business card to match our image.

We want something that is simple yet beautiful, feminine, classy, sophisticated and elegant. We want it to stand out and don't mind if it is bold.

The design should include our logo and colours of red or maroon with gold highlights. We don't mind if black is used.

Marlow & Quince

Target Market(s)

For those who like to indulge or treat themselves and give in to their temptations on good quality desserts.

Industry/Entity Type

Business

Requirements
Must have
• Must include our logo and our name

Marlow & Quince

M & Q

```html
<!DOCTYPE html>
<html lang="en">
<head>
<meta charset="utf-8">
<title>Marlow &amp; Quince — Business Card</title>
<link rel="stylesheet" href="https://fonts.googleapis.com/css2?family=Cinzel:wght@500&family=Libre+Baskerville:wght@700&family=Arimo:wght@400&display=swap">
<style>
  :root {
    --backdrop: #d9d6d2;
    --maroon: #8e1a1d;
    --maroon-deep: #5e0d10;
    --maroon-light: #b2282a;
    --gold: #e2b47a;
    --gold-soft: #c99862;
    --paper: #ffffff;
    --ink: #222222;
    --rule: #9a2a2c;
  }
  * { margin: 0; padding: 0; box-sizing: border-box; }
  html, body { width: 1200px; height: 951px; overflow: hidden; }
  body { background: var(--backdrop); position: relative; }

  .card {
    position: absolute;
    width: 560px;
    height: 320px;
    border-radius: 22px;
    box-shadow: 0 10px 28px rgba(0,0,0,.22);
    overflow: hidden;
  }

  /* Front */
  .card--front {
    left: 60px; top: 110px;
    background: radial-gradient(ellipse at 40% 45%, var(--maroon-light) 0%, var(--maroon) 45%, var(--maroon-deep) 100%);
  }
  .front__flourish {
    position: absolute;
    right: 0; top: 0;
    width: 300px; height: 96px;
    background: radial-gradient(ellipse at 60% 30%, rgba(226,180,122,.55) 0%, rgba(226,180,122,.15) 60%, rgba(226,180,122,0) 100%);
  }
  .front__brand {
    position: absolute;
    left: 40px; top: 128px;
    width: 300px;
    text-align: center;
    font-family: "Cinzel", serif;
    font-weight: 500;
    font-size: 30px;
    letter-spacing: 1px;
    color: var(--gold);
  }
  .front__web {
    position: absolute;
    left: 0; right: 0; bottom: 36px;
    text-align: center;
    font-family: "Libre Baskerville", serif;
    font-weight: 700;
    font-size: 15px;
    letter-spacing: .5px;
    color: var(--paper);
  }

  /* Back */
  .card--back {
    left: 580px; top: 500px;
    background: var(--paper);
  }
  .back__brand {
    position: absolute;
    left: 34px; top: 40px;
    width: 200px;
    text-align: center;
    font-family: "Cinzel", serif;
    font-weight: 500;
    font-size: 19px;
    color: var(--maroon);
  }
  .back__name {
    position: absolute;
    right: 30px; top: 118px;
    font-family: "Arimo", sans-serif;
    font-size: 22px;
    color: var(--maroon);
  }
  .back__rule {
    position: absolute;
    left: 30px; right: 30px; top: 148px;
    height: 1.5px;
    background: var(--rule);
  }
  .contact {
    position: absolute;
    left: 34px; top: 168px;
    list-style: none;
    font-family: "Arimo", sans-serif;
    font-size: 15px;
    color: var(--ink);
    line-height: 21px;
  }
  .contact li { display: flex; align-items: center; gap: 8px; }
  .contact svg { width: 14px; height: 14px; fill: var(--maroon); flex: none; }
  .address {
    position: absolute;
    left: 330px; top: 232px;
    display: flex; gap: 10px;
    font-family: "Arimo", sans-serif;
    font-size: 15px;
    line-height: 20px;
    color: var(--ink);
  }
  .address svg { width: 14px; height: 14px; fill: var(--maroon); margin-top: 2px; flex: none; }
</style>
</head>
<body>

<section class="card card--front">
  <div class="front__flourish" role="img" aria-label="Gold floral scroll ornament in the top corner"></div>
  <div class="front__brand">Marlow &amp; Quince</div>
  <div class="front__web">www.marlow&amp;quince.com</div>
</section>

<section class="card card--back">
  <div class="back__brand">Marlow &amp; Quince</div>
  <div class="back__name">Marlow &amp; Quince</div>
  <div class="back__rule"></div>

  <ul class="contact">
    <li>
      <svg viewBox="0 0 16 16" aria-hidden="true"><path d="M3.6 1.5l2.3 2.6-1.3 1.7c.9 2 2.5 3.6 4.5 4.5l1.7-1.3 2.6 2.3-1.4 2.2C7.4 15 1 8.6 1.5 3z"/></svg>
      512-555-0142
    </li>
    <li>
      <svg viewBox="0 0 16 16" aria-hidden="true"><rect x="2" y="5" width="12" height="8" rx="1.5"/><rect x="4" y="2" width="8" height="4"/></svg>
      512-555-0143
    </li>
    <li>
      <svg viewBox="0 0 16 16" aria-hidden="true"><path d="M1 3h14v10H1z M1 3l7 6 7-6" fill="none" stroke="#8e1a1d" stroke-width="1.6"/></svg>
      info@marlow&amp;quince.com
    </li>
    <li>
      <svg viewBox="0 0 16 16" aria-hidden="true"><circle cx="8" cy="8" r="6.5"/></svg>
      www.marlow&amp;quince.com
    </li>
  </ul>

  <div class="address">
    <svg viewBox="0 0 16 16" aria-hidden="true"><path d="M8 1.5L1 8h2v6.5h4v-4h2v4h4V8h2z"/></svg>
    <div>1450 Alder Crest Blvd.<br>Suite 210-114<br>Dalworth, TX 78011</div>
  </div>
</section>

</body>
</html>
```